Lantern Crest Pathway

I need a on page electronic flyer for this coaching program. I want a silhouette to accompany the case the copy starts with. I have the copy written but need it put together in a striking way.

Target Market(s)

towards higher net worth individuals

Industry/Entity Type

Electronic

```html
<!DOCTYPE html>
<html lang="en">
<head>
<meta charset="utf-8">
<title>Lantern Crest Pathway — Coaching Program Flyer</title>
<link rel="stylesheet" href="https://fonts.googleapis.com/css2?family=Arimo:wght@400;700&family=Tinos:wght@400;700&family=Sriracha&family=Caveat:wght@400;600&display=swap">
<style>
  :root {
    --ink: #111111;
    --band: #000000;
    --paper: #ffffff;
    --title-blue: #4fc3f0;
    --title-white: #f2f4f6;
    --leaf: #9be21f;
    --leaf-edge: #2f4a08;
    --note-green: #7bb51c;
    --bullet-blue: #1f74b8;
    --arrow-blue: #3aa6e6;
    --alert-red: #c8161d;
    --brand-blue: #1b8fd4;
    --photo-dark: #6f7378;
    --photo-light: #e9eaec;
  }
  html, body { margin: 0; padding: 0; overflow: hidden; }
  body { width: 840px; height: 1200px; background: var(--paper); }
  .flyer { position: relative; width: 840px; height: 1200px; overflow: hidden; background: var(--paper); font-family: "Arimo", Arial, sans-serif; color: var(--ink); }

  .masthead { position: absolute; left: 0; top: 0; width: 840px; height: 162px; background: var(--band); }
  .brand { position: absolute; left: 30px; top: 22px; display: flex; align-items: center; gap: 8px; }
  .brand-dot { width: 34px; height: 34px; border-radius: 50%; background: var(--brand-blue); }
  .brand-name { font-family: "Tinos", serif; font-weight: 700; font-size: 20px; color: var(--title-white); }
  .program-name { position: absolute; left: 186px; top: 62px; font-family: "Tinos", serif; font-weight: 700; font-size: 23px; color: var(--title-blue); white-space: nowrap; }
  .headline { position: absolute; left: 232px; top: 90px; margin: 0; font-family: "Tinos", serif; font-weight: 400; font-size: 29px; color: var(--title-white); white-space: nowrap; text-shadow: 0 0 6px rgba(120,200,255,.6); }

  .story { position: absolute; left: 54px; top: 176px; width: 780px; font-size: 15.2px; line-height: 20.4px; }
  .story p { margin: 0 0 20.4px; white-space: nowrap; }
  .story p.tight { margin-top: -20.4px; }

  .tagline { position: absolute; left: 52px; top: 456px; margin: 0; font-family: "Sriracha", cursive; font-weight: 400; font-size: 36px; line-height: 44px; color: var(--leaf); -webkit-text-stroke: 1.3px var(--leaf-edge); white-space: nowrap; transform: scaleX(0.82); transform-origin: left center; }

  .process { position: absolute; left: 54px; top: 514px; width: 780px; margin: 0; font-size: 15.2px; line-height: 20.4px; white-space: nowrap; }

  .portrait { position: absolute; left: 0; top: 672px; width: 324px; height: 476px; background: radial-gradient(ellipse at 30% 40%, var(--photo-dark) 0%, #b9bbbe 45%, var(--photo-light) 75%, rgba(255,255,255,0) 100%); }

  .benefits { position: absolute; left: 278px; top: 672px; margin: 0; padding: 0; list-style: none; }
  .benefits li { display: flex; align-items: center; height: 36.6px; font-size: 15.4px; color: var(--bullet-blue); white-space: nowrap; }
  .benefits svg { width: 32px; height: 26px; margin-right: 6px; flex: none; }

  .question { position: absolute; left: 144px; top: 826px; font-family: "Tinos", serif; font-size: 21.5px; color: var(--alert-red); text-decoration: underline; white-space: nowrap; }

  .bio-arrow { position: absolute; left: 300px; top: 870px; width: 28px; height: 24px; }
  .bio { position: absolute; right: 14px; top: 864px; width: 500px; margin: 0; font-family: "Caveat", cursive; font-style: italic; font-size: 23px; line-height: 29px; color: var(--note-green); text-align: right; white-space: nowrap; }

  .offer-arrow { position: absolute; left: 348px; top: 960px; width: 54px; height: 70px; }
  .offer { position: absolute; left: 396px; top: 960px; font-family: "Caveat", cursive; font-size: 21px; line-height: 29px; color: var(--ink); white-space: nowrap; }
  .offer-title { margin: 0; }
  .offer ul { margin: 0; padding: 0 0 0 44px; list-style: none; }

  .footer { position: absolute; left: 0; top: 1148px; width: 840px; height: 52px; background: var(--band); }
  .footer-name { position: absolute; left: 18px; top: 8px; font-family: "Caveat", cursive; font-weight: 600; font-size: 30px; line-height: 36px; color: var(--alert-red); white-space: nowrap; }
  .footer-contact { position: absolute; right: 8px; top: 13px; font-family: "Caveat", cursive; font-size: 19px; line-height: 26px; color: var(--title-white); white-space: nowrap; }
</style>
</head>
<body>
<main class="flyer">
  <header class="masthead">
    <div class="brand"><span class="brand-dot"></span><span class="brand-name">Harbor Circle</span></div>
    <div class="program-name">“Lantern Crest Pathway”</div>
    <h1 class="headline">From Financial Worries to Wealth Satisfaction</h1>
  </header>

  <section class="story">
    <p>A 49 year old attorney, Steve was used to success and rising net worth. But with huge losses in the<br>market crash, layoffs at his firm, his kids heading for college and the stagnant economy stretching<br>ahead, his usual optimism is gone. With his anxiety growing, Steve doubts his own decision making<br>ability. His confidence slipping, he stopped opening his financial statements and could barely speak<br>to his financial advisor. He thought if his advisor said “hang in there” one more time, he just might<br>blow up.</p>
    <p>Yet Steve felt too embarrassed to talk about his deep worries, even with his wife. It seemed like<br>all he could do was pour another glass of wine and suffer in isolation.</p>
    <p class="tight">If you’re like Steve, you’re afraid and alone with plenty of company. In a September 2009 American<br>Mindwell Council poll, 80 percent reported the economy is causing significant stress, up<br>from 66 percent from the previous April. The National Rest Institute said 27 percent of people<br>surveyed had sleeplessness because of economic anxiety.</p>
  </section>

  <h2 class="tagline">Sometimes the best financial advice isn’t about numbers...</h2>

  <p class="process">This process guides you to step back and understand the source of your financial worry—your unique<br>story about the meaning of money. Your money story drives your emotions and decision making—for<br>better and worse. You’ll learn a decision making tool for more conscious, effective and satisfying<br>financial and life decisions. You’ll also examine your core values and strengths—what really matters<br>most to you and how you work at your best. When you use your money and your core strengths to<br>pursue your highest aspirations, life and wealth become balanced. As you commit more fully to your<br>mission and passions, satisfaction grows and money worries melt away.</p>

  <div class="portrait" role="img" aria-label="Black and white portrait of a pensive young man in a knit cap beside a dark handprint"></div>

  <ul class="benefits">
    <li><svg viewBox="0 0 34 28"><polygon points="2,2 32,14 2,26" fill="var(--arrow-blue)"/></svg>Learn a decision making tool to make choices that truly serve your needs.</li>
    <li><svg viewBox="0 0 34 28"><polygon points="2,2 32,14 2,26" fill="var(--arrow-blue)"/></svg>Clarify and more fully engage with your purpose and passions.</li>
    <li><svg viewBox="0 0 34 28"><polygon points="2,2 32,14 2,26" fill="var(--arrow-blue)"/></svg>Improve your relationship with your financial advisor.</li>
    <li><svg viewBox="0 0 34 28"><polygon points="2,2 32,14 2,26" fill="var(--arrow-blue)"/></svg>Feel more in control and confident in your financial life.</li>
  </ul>

  <div class="question">How can you take control of these worries and get back to enjoying your life?</div>

  <svg class="bio-arrow" viewBox="0 0 32 26"><polygon points="1,8 16,8 16,1 31,13 16,25 16,18 1,18" fill="var(--leaf)"/></svg>
  <p class="bio">Dale Morrow, Ph.D. is a psychologist with 30 years of experience<br>treating anxiety and stress. He is co-founder and facilitator of<br>Harbor Circle, a peer learning group for high net worth investors.</p>

  <svg class="offer-arrow" viewBox="0 0 54 70"><path d="M8 4 C4 28 12 42 30 50" stroke="var(--arrow-blue)" stroke-width="9" fill="none" stroke-linecap="round"/><polygon points="24,38 48,58 18,64" fill="var(--arrow-blue)"/></svg>
  <div class="offer">
    <p class="offer-title">&nbsp;&nbsp;&nbsp;&nbsp;A Six Week Program to :</p>
    <ul>
      <li>Reduce stress</li>
      <li>Improve performance</li>
      <li>Restore Control</li>
      <li>$995 Money Back Guarantee</li>
      <li>Dale Morrow (555)014-2290</li>
    </ul>
  </div>

  <footer class="footer">
    <div class="footer-name">“Steven” Alder Falls, PA</div>
    <div class="footer-contact">For more information, call 555-013-7788 &nbsp;dmorrow@harborcircle.example</div>
  </footer>
</main>
</body>
</html>
```